Request for Business Card Design

Hi. My name is Marlene, I am looking for a new business card design for my company, Quarrow Signal Instruments, LLC. I really like the design you did for Tarsel Venture and was hoping you could do something similar using our full logo and our mark. I am also open to any raised texture design using our mark. I have attached our full logo, which would need to be somewhere on the card, as well as the mark in both outline and full form, as well as our brand colors / guide. The card does not have to be white, as long as our logo and mark appear. I actually like darker colored business cards more, but am open to all options. If you are interested in working with me, please let me know. We would also take the business card design into letterhead design if you can do that.

```html
<!DOCTYPE html>
<html lang="en">
<head>
<meta charset="utf-8">
<title>Quarrow Signal Instruments – Business Card</title>
<link href="https://fonts.googleapis.com/css2?family=Open+Sans:wght@400;600;700;800&display=swap" rel="stylesheet">
<style>
  :root {
    --bg: #232323;
    --card-dark: #3d3d3f;
    --brand-blue: #1a9bc4;
    --brand-blue-deep: #127ea3;
    --text-light: #ffffff;
    --front-type: #8fd3e4;
  }
  * { box-sizing: border-box; margin: 0; padding: 0; }
  html, body { width: 1200px; height: 780px; overflow: hidden; background: var(--bg); }
  body { font-family: "Open Sans", sans-serif; position: relative; }

  .card {
    position: absolute; top: 92px; width: 340px; height: 595px;
    border-radius: 22px; overflow: hidden;
    box-shadow: 0 10px 28px rgba(0,0,0,0.55);
  }
  .card--front { left: 220px; background: var(--brand-blue); }
  .card--back { left: 640px; background: var(--card-dark); color: var(--text-light); }

  /* Front */
  .front-brand {
    position: absolute; left: 50%; top: 50%;
    transform: translate(-50%, -50%) rotate(-90deg);
    display: flex; align-items: center; gap: 22px; white-space: nowrap;
  }
  .front-brand__dot { width: 70px; height: 70px; border-radius: 50%; background: var(--brand-blue-deep); flex: none; }
  .front-brand__name {
    font-weight: 800; font-size: 34px; line-height: 1.05; letter-spacing: 1px;
    color: var(--front-type); text-transform: uppercase;
  }

  /* Back */
  .back-brand { position: absolute; left: 28px; top: 30px; display: flex; align-items: center; gap: 12px; }
  .back-brand__dot { width: 30px; height: 30px; border-radius: 50%; background: var(--brand-blue); }
  .back-brand__name { font-weight: 800; font-size: 15px; line-height: 1.1; letter-spacing: 1px; text-transform: uppercase; color: var(--text-light); }

  .person { position: absolute; top: 288px; width: 100%; text-align: center; }
  .person__name { font-weight: 800; font-size: 36px; color: var(--brand-blue); line-height: 1; }
  .person__role { font-weight: 600; font-size: 15px; margin-top: 2px; }

  .contact-frame { position: absolute; left: 0; top: 0; width: 340px; height: 595px; }

  .contact-list { position: absolute; top: 384px; width: 100%; text-align: center; list-style: none; font-size: 15px; line-height: 22px; }
  .contact-list li.gap { margin-top: 8px; }

  .address { position: absolute; top: 540px; width: 100%; text-align: center; font-size: 15px; line-height: 21px; }
</style>
</head>
<body>

<section class="card card--front" aria-label="Card front">
  <div class="front-brand">
    <span class="front-brand__dot"></span>
    <span class="front-brand__name">Quarrow<br>Signal Instruments</span>
  </div>
</section>

<section class="card card--back" aria-label="Card back">
  <div class="back-brand">
    <span class="back-brand__dot"></span>
    <span class="back-brand__name">Quarrow<br>Signal Instruments</span>
  </div>

  <div class="person">
    <h1 class="person__name">Marlene</h1>
    <p class="person__role">Director</p>
  </div>

  <svg class="contact-frame" viewBox="0 0 340 595" aria-hidden="true">
    <g fill="none" stroke="#1a9bc4" stroke-width="2">
      <polyline points="113,358 20,358 20,455 38,455"/>
      <polyline points="227,358 320,358 320,477 302,477"/>
      <polyline points="143,372 60,372 60,395 74,395"/>
      <polyline points="197,372 280,372 280,417 266,417"/>
    </g>
    <g fill="#1a9bc4">
      <polygon points="38,450 46,455 38,460"/>
      <polygon points="302,472 294,477 302,482"/>
      <polygon points="74,390 82,395 74,400"/>
      <polygon points="266,412 258,417 266,422"/>
      <circle cx="125" cy="358" r="12"/>
      <circle cx="155" cy="358" r="12"/>
      <circle cx="185" cy="358" r="12"/>
      <circle cx="215" cy="358" r="12"/>
      <circle cx="170" cy="522" r="12"/>
    </g>
    <g fill="none" stroke="#fff" stroke-width="1.4">
      <rect x="119" y="354" width="12" height="8"/>
      <polyline points="119,354 125,359 131,354"/>
      <path d="M150 353 q2 -2 4 0 l-1 3 q2 3 4 4 l3 -1 q2 2 0 4 q-6 1 -10 -10z"/>
      <rect x="179" y="355" width="12" height="8"/>
      <rect x="182" y="351" width="6" height="4"/>
      <circle cx="215" cy="358" r="6"/>
      <line x1="209" y1="358" x2="221" y2="358"/>
      <ellipse cx="215" cy="358" rx="2.5" ry="6"/>
      <path d="M170 529 l-4 -6 a5 5 0 1 1 8 0z"/>
    </g>
  </svg>

  <ul class="contact-list">
    <li>+001 555 210 4837</li>
    <li>+001 555 210 4890</li>
    <li class="gap">info@quarrowsignal.com</li>
    <li>www.quarrowsignal.com</li>
  </ul>

  <address class="address" style="font-style:normal">
    1180 Ledger Point Avenue<br>Fairhaven, CO 80611
  </address>
</section>

</body>
</html>
```